Create a Big Data Website that is professional but has a creative flare to it.

I am after a modern business design for a company in the Big Data space however it still needs to have a wow value and something stand out from other corporate websites.
My competitors websites are to give you and idea of content:
www.tarnvilla.com
www.pluvoria.com
www.meridu4.com.au
www.quornaby.com
I have uploaded my company Logo so you can use that to make sure it matches your theme.

Target Market(s)

Banks, Insurance Companies, Government, Gas and Energy Companies and Food Manufacturing.

Industry/Entity Type

Consulting

Coding

Number of Pages Required

5+ page

Colors

Designer to choose colors to be used in the design.

Requirements
Must have
• Images, Diagrams around Big Data. Usage of information or graphs from sources like Velsham are fine to use.
Nice to have
• Interactive design use mouse overs, change in text, highlighting information for clear focus.
Should not have
• Cluttered Pages of Informaiton

```html
<!DOCTYPE html>
<html lang="en">
<head>
<meta charset="utf-8">
<title>Veradyne Consulting Services</title>
<link href="https://fonts.googleapis.com/css2?family=Roboto:wght@400;500;700&family=Open+Sans:ital,wght@0,400;0,600;0,700;1,400&display=swap" rel="stylesheet">
<style>
:root{
  --navy:#1b3f73;
  --navy-deep:#163463;
  --brand:#1a4f8c;
  --sky:#1e8fd9;
  --sky-light:#2fa0e6;
  --ink:#222;
  --muted:#666;
  --line:#e3e3e3;
  --white:#fff;
}
*{margin:0;padding:0;box-sizing:border-box}
html,body{width:1200px;height:3232px;overflow:hidden;background:var(--white)}
body{font-family:"Open Sans",sans-serif;color:var(--ink);position:relative}
.abs{position:absolute}
h1,h2,h3,h4{font-family:"Roboto",sans-serif}

/* header */
.topbar{left:0;top:0;width:1200px;height:4px;background:var(--navy)}
.lang{left:900px;top:0;width:150px;height:24px;background:var(--navy);color:#fff;font-size:12px;line-height:24px;padding-left:36px;clip-path:polygon(0 0,100% 0,92% 100%,8% 100%)}
.brand{left:100px;top:12px;display:flex;align-items:center;gap:12px}
.brand-mark{width:60px;height:46px;border-radius:6px;background:var(--brand)}
.brand-name{font-family:"Roboto",sans-serif;font-weight:700;color:var(--brand);font-size:38px;line-height:1}
.brand-sub{font-family:"Roboto",sans-serif;font-weight:700;color:var(--brand);font-size:14px;letter-spacing:1.5px}
.nav{left:490px;top:46px;display:flex;gap:30px;font-family:"Roboto",sans-serif;font-size:16px;font-weight:500;color:#222}
.nav .active{color:var(--brand)}
.header-rule{left:0;top:86px;width:1200px;height:1px;background:var(--line)}

/* hero */
.hero{left:0;top:87px;width:1200px;height:478px;background:radial-gradient(ellipse at 70% 30%,#3b8fd0 0%,#1a3f6e 22%,#0c1c33 55%,#07101e 100%)}
.hero-title{left:97px;top:245px;color:#fff;font-size:46px;font-weight:700}
.hero-sub{left:97px;top:310px;color:#fff;font-size:34px;font-weight:500;font-family:"Roboto",sans-serif}
.btn-outline{border:2px solid #fff;border-radius:6px;color:#fff;font-family:"Roboto",sans-serif;font-weight:700;font-size:15px;text-align:center}
.hero-btn{left:99px;top:373px;width:126px;height:40px;line-height:36px}
.arrow-btn{width:38px;height:38px;border:2px solid #fff;border-radius:6px;display:flex;align-items:center;justify-content:center}

/* welcome */
.section-title{width:1200px;left:0;text-align:center;font-size:30px;font-weight:500;color:#222}
.lead{left:170px;width:860px;text-align:center;font-size:13px;line-height:24px;color:var(--muted)}
.card{width:306px;height:312px;border:1px solid #ddd;text-align:center}
.hex{width:98px;height:88px;margin:36px auto 0}
.card h3{font-size:20px;font-weight:500;margin-top:24px}
.card p{font-size:13px;line-height:23px;color:var(--muted);margin-top:6px;padding:0 40px}
.more{font-family:"Roboto",sans-serif;font-weight:700;color:var(--brand);font-size:15px;margin-top:16px;display:block}

/* why */
.why-title{left:97px;top:1160px;font-size:30px;font-weight:700}
.why-lead{left:97px;top:1218px;width:460px;font-size:13px;line-height:23px;color:var(--muted)}
.feature{left:97px;display:flex;gap:22px;align-items:center}
.feature h4{font-size:19px;font-weight:500}
.feature p{font-size:13px;color:var(--muted);margin-top:6px}
.why-photo{left:612px;top:1152px;width:487px;height:362px;background:linear-gradient(135deg,#2a3a4a,#6a7b86 45%,#c8a16b 80%,#3b3125);border:3px solid #eee}

/* solutions band */
.band{left:0;top:1590px;width:1200px;height:461px;background:var(--sky)}
.solutions-art{left:96px;top:1637px;width:368px;height:348px;background:radial-gradient(circle at 50% 50%,#1d5fa6 0%,#2b8fd4 45%,#47a6e2 100%);clip-path:polygon(25% 0,75% 0,100% 50%,75% 100%,25% 100%,0 50%)}
.solutions-label{left:196px;top:1778px;width:168px;text-align:center;color:#fff;font-family:"Roboto",sans-serif;font-weight:700;font-size:21px;line-height:27px}
.band-title{left:553px;top:1718px;color:#fff;font-size:32px;font-weight:500}
.band-text{left:553px;top:1772px;width:460px;color:#fff;font-size:16.5px;font-weight:600;line-height:24px}
.band-btn{left:553px;top:1897px;width:128px;height:40px;line-height:36px}

/* blog */
.post{width:308px;height:226px;border:1px solid #ddd;padding:4px}
.post-img{width:100%;height:100%}
.post-cap{position:absolute;left:50%;transform:translateX(-50%);bottom:6px;width:198px;height:54px;background:rgba(120,120,120,.85);color:#fff;text-align:center}
.post-cap b{font-family:"Roboto",sans-serif;font-weight:500;font-size:19px;display:block;margin-top:2px}
.post-cap span{font-size:13px}
.side-arrow{width:42px;height:42px;border:1px solid #bbb;border-radius:8px;display:flex;align-items:center;justify-content:center;background:#fff}

/* testimonials */
.testi{left:0;top:2482px;width:1200px;height:336px;background:var(--navy)}
.testi-photo{left:0;top:2482px;width:600px;height:336px;background:linear-gradient(120deg,#0a1528,#1d3f78 55%,#0d1a30);clip-path:polygon(0 0,100% 0,440px 100%,0 100%)}
.testi-edge{left:0;top:2482px;width:605px;height:336px;background:var(--sky-light);clip-path:polygon(592px 0,605px 0,452px 100%,439px 100%)}
.testi-title{left:650px;top:2536px;color:#fff;font-size:30px;font-weight:500}
.quote-badge{left:584px;top:2588px;width:54px;height:54px;border-radius:50%;border:2px solid #fff;display:flex;align-items:center;justify-content:center;color:#fff;font-family:Georgia,serif;font-size:42px;line-height:1;padding-top:18px}
.testi-name{left:656px;top:2604px;color:#fff;font-family:"Roboto",sans-serif;font-weight:700;font-size:16px}
.testi-text{left:584px;top:2674px;width:476px;color:#fff;font-style:italic;font-size:14px;line-height:28px}
.mini-arrow{width:24px;height:24px;border-radius:4px;background:var(--sky-light);display:flex;align-items:center;justify-content:center}

/* footer */
.social{left:99px;top:2998px;display:flex;gap:10px}
.social span{width:34px;height:34px;border:1px solid #c9c9c9;border-radius:6px;display:block;position:relative}
.social span::after{content:"";position:absolute;left:11px;top:11px;width:10px;height:10px;border-radius:2px;background:var(--brand)}
.foot-col h4{font-size:16px;font-weight:500;color:#222}
.foot-col ul{list-style:none;margin-top:14px}
.foot-col li{font-size:13px;color:#444;line-height:23px}
.email{left:831px;top:2952px;width:268px;height:34px;border:1px solid #ccc;font-size:12px;color:#999;padding:8px 12px}
.submit{left:994px;top:3003px;width:105px;height:34px;border-radius:8px;background:var(--navy);color:#fff;font-family:"Roboto",sans-serif;font-weight:700;font-size:15px;text-align:center;line-height:34px}
.foot-rule{left:97px;top:3145px;width:1005px;height:1px;background:#ccc}
.copyright{left:0;top:3172px;width:1200px;text-align:center;font-size:13px;color:#444}
</style>
</head>
<body>

<!-- header -->
<div class="abs topbar"></div>
<div class="abs lang">Language &nbsp;&nbsp;&#8964;</div>
<div class="abs brand">
  <div class="brand-mark"></div>
  <div>
    <div class="brand-name">Veradyne</div>
    <div class="brand-sub">CONSULTING SERVICES</div>
  </div>
</div>
<nav class="abs nav">
  <span class="active">Home</span><span>About Us</span><span>Services</span><span>Clients</span><span>Solutions</span><span>Blog</span><span>Contact Us</span>
  <svg width="16" height="16" viewBox="0 0 16 16"><circle cx="6.5" cy="6.5" r="5" fill="none" stroke="#222" stroke-width="2"/><line x1="10.5" y1="10.5" x2="15" y2="15" stroke="#222" stroke-width="2"/></svg>
</nav>
<div class="abs header-rule"></div>

<!-- hero -->
<div class="abs hero" role="img" aria-label="Hand holding a glowing digital globe of data connections"></div>
<h1 class="abs hero-title">VERADYNE CONSULTING</h1>
<div class="abs hero-sub">We Provide You All Big Data Services</div>
<div class="abs btn-outline hero-btn">Join Us !</div>
<div class="abs arrow-btn" style="left:26px;top:306px"><svg width="12" height="16"><path d="M9 2 3 8l6 6" stroke="#fff" stroke-width="2.5" fill="none"/></svg></div>
<div class="abs arrow-btn" style="left:1134px;top:306px"><svg width="12" height="16"><path d="M3 2l6 6-6 6" stroke="#fff" stroke-width="2.5" fill="none"/></svg></div>

<!-- welcome -->
<h2 class="abs section-title" style="top:630px">Welcome To Veradyne Consulting</h2>
<p class="abs lead" style="top:690px">Lorem ipsum dolor sit amet, consectetur adipiscing elit, sed do eiusmod tempor incididunt ut labore et dolore magna aliqua. Ut enim ad minim veniam, quis nostrud exercitation ullamco laboris nisi ut aliquip ex ea commodo consequat.</p>

<div class="abs card" style="left:97px;top:769px">
  <svg class="hex" viewBox="0 0 98 88"><polygon points="25,2 73,2 96,44 73,86 25,86 2,44" fill="none" stroke="#1a4f8c" stroke-width="2.5"/><rect x="32" y="30" width="34" height="24" fill="none" stroke="#1a4f8c" stroke-width="3"/><path d="M36 46l8-8 6 6 10-10" stroke="#1a4f8c" stroke-width="2.5" fill="none"/></svg>
  <h3>Data Analysis</h3>
  <p>There are many variations of pass of Lorem Ipsum available, but majority have suffered alteration.</p>
  <span class="more">Read More &raquo;</span>
</div>
<div class="abs card" style="left:448px;top:769px">
  <svg class="hex" viewBox="0 0 98 88"><polygon points="25,2 73,2 96,44 73,86 25,86 2,44" fill="none" stroke="#1a4f8c" stroke-width="2.5"/><circle cx="49" cy="42" r="14" fill="#1a4f8c"/><rect x="43" y="56" width="12" height="8" fill="#1a4f8c"/><text x="49" y="48" fill="#fff" font-size="16" text-anchor="middle" font-family="Roboto,sans-serif" font-weight="700">$</text></svg>
  <h3>Business Intellegence</h3>
  <p>There are many variations of pass of Lorem Ipsum available, but majority have suffered alteration.</p>
  <span class="more">Read More &raquo;</span>
</div>
<div class="abs card" style="left:797px;top:769px">
  <svg class="hex" viewBox="0 0 98 88"><polygon points="25,2 73,2 96,44 73,86 25,86 2,44" fill="none" stroke="#1a4f8c" stroke-width="2.5"/><circle cx="47" cy="46" r="16" fill="#1a4f8c"/><circle cx="47" cy="46" r="9" fill="#fff"/><circle cx="47" cy="46" r="4" fill="#1a4f8c"/><path d="M47 46 64 29" stroke="#1a4f8c" stroke-width="3"/></svg>
  <h3>Commercial Strategy</h3>
  <p>There are many variations of pass of Lorem Ipsum available, but majority have suffered alteration.</p>
  <span class="more">Read More &raquo;</span>
</div>

<!-- why choose us -->
<h2 class="abs why-title">Why Choose Us ?</h2>
<p class="abs why-lead">Lorem Ipsum has been the industry's standard dummy text ever since the 1500s, when an unknown printer took a galley of type.</p>
<div class="abs feature" style="top:1272px">
  <svg width="64" height="58" viewBox="0 0 64 58"><polygon points="16,2 48,2 62,29 48,56 16,56 2,29" fill="none" stroke="#1a4f8c" stroke-width="2"/><rect x="20" y="18" width="24" height="22" fill="none" stroke="#1a4f8c" stroke-width="2"/><path d="M29 25l-4 4 4 4M35 25l4 4-4 4" stroke="#1a4f8c" stroke-width="2" fill="none"/></svg>
  <div><h4>Excellent Coding</h4><p>Lorem Ipsum has been the industry's standard.</p></div>
</div>
<div class="abs feature" style="top:1348px">
  <svg width="64" height="58" viewBox="0 0 64 58"><polygon points="16,2 48,2 62,29 48,56 16,56 2,29" fill="none" stroke="#1a4f8c" stroke-width="2"/><circle cx="32" cy="29" r="12" fill="none" stroke="#1a4f8c" stroke-width="3" stroke-dasharray="4 2"/><circle cx="32" cy="29" r="4" fill="#1a4f8c"/></svg>
  <div><h4>Quality Support</h4><p>Lorem Ipsum has been the industry's standard.</p></div>
</div>
<div class="abs feature" style="top:1424px">
  <svg width="64" height="58" viewBox="0 0 64 58"><polygon points="16,2 48,2 62,29 48,56 16,56 2,29" fill="none" stroke="#1a4f8c" stroke-width="2"/><ellipse cx="32" cy="19" rx="10" ry="4" fill="none" stroke="#1a4f8c" stroke-width="2"/><path d="M22 19v20c0 5 20 5 20 0V19M22 26c0 5 20 5 20 0M22 33c0 5 20 5 20 0" fill="none" stroke="#1a4f8c" stroke-width="2"/></svg>
  <div><h4>Data Warehousing</h4><p>Lorem Ipsum has been the industry's standard.</p></div>
</div>
<div class="abs why-photo" role="img" aria-label="Team of analysts studying floating data charts on a transparent screen"></div>

<!-- solutions band -->
<div class="abs band"></div>
<div class="abs solutions-art" role="img" aria-label="Hexagonal illustration of big data solution areas: analytics, cloud, reporting, growth charts, networks and dashboards"></div>
<div class="abs solutions-label">We Provide<br>Solutions<br>For</div>
<h2 class="abs band-title">Data Collection</h2>
<p class="abs band-text">There are many variations of passages of Lorem Ipsum available, but the majority have suffered alteration in some form, by injected humour, or randomised words which don't look even slightly believable.</p>
<div class="abs btn-outline band-btn">Read More</div>

<!-- blog -->
<h2 class="abs section-title" style="top:2108px">Our Blog</h2>
<div class="abs side-arrow" style="left:24px;top:2267px"><svg width="12" height="16"><path d="M9 2 3 8l6 6" stroke="#555" stroke-width="2" fill="none"/></svg></div>
<div class="abs side-arrow" style="left:1134px;top:2267px"><svg width="12" height="16"><path d="M3 2l6 6-6 6" stroke="#555" stroke-width="2" fill="none"/></svg></div>

<div class="abs post" style="left:101px;top:2176px">
  <div class="post-img" role="img" aria-label="Businessman facing a wall of world map and data charts" style="background:linear-gradient(160deg,#d8e3ee,#9fb6cc 60%,#5f7a96)"></div>
  <div class="post-cap"><b>Contrary To Belief</b><span>&#128197; 10 Days Ago &nbsp;| &#128172; 33</span></div>
</div>
<div class="abs post" style="left:446px;top:2176px">
  <div class="post-img" role="img" aria-label="Hands holding a tablet showing business charts" style="background:linear-gradient(160deg,#5a4030,#b8a38c 50%,#e6e2dc)"></div>
  <div class="post-cap"><b>Contrary To Belief</b><span>&#128197; 10 Days Ago &nbsp;| &#128172; 33</span></div>
</div>
<div class="abs post" style="left:791px;top:2176px">
  <div class="post-img" role="img" aria-label="Colleagues meeting around a table with a laptop" style="background:linear-gradient(160deg,#e8e4df,#b59a82 50%,#6d5a4d)"></div>
  <div class="post-cap"><b>Contrary To Belief</b><span>&#128197; 10 Days Ago &nbsp;| &#128172; 33</span></div>
</div>

<!-- testimonials -->
<div class="abs testi"></div>
<div class="abs testi-photo" role="img" aria-label="Hand presenting glowing holographic charts and graphs"></div>
<div class="abs testi-edge"></div>
<h2 class="abs testi-title">Client Testimonials</h2>
<div class="abs quote-badge">&ldquo;</div>
<div class="abs testi-name">Marcus Ellery</div>
<p class="abs testi-text">There are many variations of passages of Lorem Ipsum available, but the majority have suffered alteration in some form, by injected humour, or randomised words which don't look even slightly believable.</p>
<div class="abs mini-arrow" style="left:1040px;top:2741px"><svg width="8" height="10"><path d="M6 1 2 5l4 4" stroke="#fff" stroke-width="2" fill="none"/></svg></div>
<div class="abs mini-arrow" style="left:1075px;top:2741px"><svg width="8" height="10"><path d="M2 1l4 4-4 4" stroke="#fff" stroke-width="2" fill="none"/></svg></div>

<!-- footer -->
<div class="abs brand" style="top:2906px">
  <div class="brand-mark"></div>
  <div>
    <div class="brand-name">Veradyne</div>
    <div class="brand-sub">CONSULTING SERVICES</div>
  </div>
</div>
<div class="abs social"><span></span><span></span><span></span><span></span></div>

<div class="abs foot-col" style="left:487px;top:2910px">
  <h4>Quick Links</h4>
  <ul><li>Home</li><li>About Us</li><li>Services</li><li>Clients</li><li>Solutions</li><li>Blog</li><li>Contact Us</li></ul>
</div>
<div class="abs foot-col" style="left:669px;top:2906px">
  <h4>Extras</h4>
  <ul><li>FAQ</li><li>Contact Us</li><li>Statistics</li><li>Big Data Guide</li><li>Big Data Framework</li></ul>
</div>
<div class="abs foot-col" style="left:831px;top:2910px"><h4>Newsletter Subscription</h4></div>
<div class="abs email">Email</div>
<div class="abs submit">Submit</div>

<div class="abs foot-rule"></div>
<p class="abs copyright">Copyright &copy; 2017, Veradyne Consulting Services. All Rights Reserved.</p>

</body>
</html>
```